Boutique custom software development company needs new business card

Our nearly 20 year old custom software development company would like to better include the fact that we are now providing Bitcoin services. These new services are B2B include education (how to acquire and securely hold Bitcoin) and integrating Bitcoin payments into existing ecommerce sites or other existing systems. Please keep the card clean and simple. Attached is our current design and some other files. vextorial.com

Target Market(s)

businesses owners interested in long term relationship

Industry/Entity Type

Custom software development and Bitcoin

Contact Information for Business Card

Dale Parker, dale@vextorial.com, vextorial.com, (888) 555-VXTRL

Font styles to use
Other font styles liked:
• monospace

Requirements
Must have
• double-sided
Nice to have
• clean and simple
Should not have
• physical address

```html
<!DOCTYPE html>
<html lang="en">
<head>
<meta charset="utf-8">
<title>Vextorial business card</title>
<link href="https://fonts.googleapis.com/css2?family=Montserrat:wght@400;500;700;800&family=Lato:ital,wght@0,400;1,400&display=swap" rel="stylesheet">
<style>
  :root {
    --brand-blue: #4072b8;
    --brand-orange: #f07a22;
    --ink: #3d3d3d;
    --paper: #ffffff;
    --stage: #2a2a2a;
  }
  * { margin: 0; padding: 0; box-sizing: border-box; }
  html, body { width: 1200px; height: 900px; overflow: hidden; background: var(--stage); }
  .canvas {
    width: 1200px; height: 900px;
    display: flex; flex-direction: column; align-items: center; justify-content: center; gap: 24px;
  }
  .card {
    position: relative; width: 700px; height: 400px; overflow: hidden;
    box-shadow: 0 10px 30px rgba(0,0,0,.45);
  }
  .card--front { background: var(--paper); }
  .card--back { background: var(--brand-blue); display: flex; align-items: center; justify-content: center; }

  .edge-bands { position: absolute; left: 0; bottom: 0; width: 700px; height: 40px; }

  .brand { position: absolute; left: 60px; top: 140px; width: 310px; }
  .brand__name {
    font-family: "Montserrat", sans-serif; font-weight: 800; font-size: 46px;
    color: var(--brand-blue); letter-spacing: -1px; line-height: 1;
  }
  .brand__tagline {
    font-family: "Lato", sans-serif; font-style: italic; font-size: 17px; line-height: 1.35;
    color: var(--brand-blue); margin-top: 8px;
  }
  .brand__service { color: var(--brand-orange); }

  .divider { position: absolute; left: 382px; top: 120px; width: 2px; height: 140px; background: var(--brand-blue); }

  .contact { position: absolute; left: 410px; top: 128px; }
  .contact__name {
    font-family: "Montserrat", sans-serif; font-weight: 700; font-size: 24px;
    color: var(--brand-blue); text-transform: uppercase; margin-bottom: 18px;
  }
  .contact__list { list-style: none; }
  .contact__item {
    display: flex; align-items: center; gap: 10px; margin-bottom: 8px;
    font-family: "Montserrat", sans-serif; font-weight: 500; font-size: 17px; color: var(--ink);
  }
  .contact__icon { width: 16px; height: 16px; flex: none; }

  .back-brand { display: flex; flex-direction: column; align-items: center; gap: 14px; }
  .back-brand__row { display: flex; align-items: center; gap: 18px; }
  .back-brand__mark { width: 34px; height: 34px; background: var(--brand-orange); }
  .back-brand__name {
    font-family: "Montserrat", sans-serif; font-weight: 800; font-size: 58px;
    color: var(--paper); letter-spacing: -1px;
  }
  .back-brand__services {
    font-family: "Montserrat", sans-serif; font-weight: 500; font-size: 17px;
    color: var(--paper); letter-spacing: 2px; text-transform: uppercase;
  }
</style>
</head>
<body>
<main class="canvas">
  <section class="card card--front">
    <div class="brand">
      <div class="brand__name">VEXTORIAL</div>
      <div class="brand__tagline">
        developer of custom applications<br>
        <span class="brand__service">Bitcoin payments &amp; education</span>
      </div>
    </div>
    <div class="divider"></div>
    <div class="contact">
      <div class="contact__name">Dale Parker</div>
      <ul class="contact__list">
        <li class="contact__item">
          <svg class="contact__icon" viewBox="0 0 16 16"><path d="M4 1 L6.5 4 L5 6 Q6.5 9.5 10 11 L12 9.5 L15 12 L13 15 Q3 14 1 3 Z" fill="var(--brand-orange)"/></svg>
          (888) 555-VXTRL
        </li>
        <li class="contact__item">
          <svg class="contact__icon" viewBox="0 0 16 16"><rect x="1" y="3" width="14" height="10" fill="var(--brand-orange)"/><path d="M1 3 L8 9 L15 3" fill="none" stroke="#fff" stroke-width="1.4"/></svg>
          dale@vextorial.com
        </li>
        <li class="contact__item">
          <svg class="contact__icon" viewBox="0 0 16 16"><circle cx="8" cy="8" r="7" fill="var(--brand-orange)"/><path d="M1 8 H15 M8 1 Q4 8 8 15 M8 1 Q12 8 8 15" fill="none" stroke="#fff" stroke-width="1"/></svg>
          www.vextorial.com
        </li>
      </ul>
    </div>
    <svg class="edge-bands" viewBox="0 0 700 40" preserveAspectRatio="none">
      <polygon points="0,22 300,22 295,30 0,30" fill="var(--brand-blue)"/>
      <polygon points="310,22 700,22 700,40 300,40" fill="var(--brand-orange)"/>
    </svg>
  </section>

  <section class="card card--back">
    <div class="back-brand">
      <div class="back-brand__row">
        <span class="back-brand__mark"></span>
        <span class="back-brand__name">VEXTORIAL</span>
      </div>
      <div class="back-brand__services">Custom Software · Bitcoin Services</div>
    </div>
  </section>
</main>
</body>
</html>
```